Business Landing Page for SEO Company

Need the landing page of the website designed - I will provide the copy, will need to include details of my company and the services offered, about us, testimonials, faq, etc., and all these elements will need to be arranged graphically on the page.

I want something similar to this: https://torvanequill.com/

Not in terms of color or theme or anything, but we offer a similar service and want to display similar information.

Th services we provide are:

Premium Links
Monthly Links Subscription
Link Insertions

Need to advertise them on the front page. Additionally need a place for testimonials, company details, etc.,

We already have logo for the website. Please use the attached file to insert the logo within the overal design.

Target Market(s)

SEO marketers and agencies

Number of Pages Required

1 page

```html
<!DOCTYPE html>
<html lang="en">
<head>
<meta charset="utf-8">
<title>Linkora – SEO Links</title>
<link rel="stylesheet" href="https://fonts.googleapis.com/css2?family=Montserrat:wght@400;500;600;700&display=swap">
<style>
:root{
  --blue:#1f6fd8;
  --navy:#06225e;
  --orange:#ff8a0d;
  --ink:#222831;
  --grey:#6b6f78;
  --pale:#f1f5fb;
  --line:#cfdcf0;
  --white:#ffffff;
  --black:#050505;
}
*{box-sizing:border-box;margin:0;padding:0}
html,body{width:1200px;height:4819px;overflow:hidden}
body{font-family:'Montserrat',sans-serif;color:var(--ink);background:var(--white);position:relative}
.section{position:absolute;left:0;width:1200px}
.heading{position:absolute;left:0;width:1200px;text-align:center;font-weight:600;font-size:31px;letter-spacing:.3px}
.rule{position:absolute;left:567px;width:66px;height:3px;background:var(--orange)}
/* header */
.site-header{top:0;height:88px;background:var(--white)}
.brand{position:absolute;left:112px;top:20px;font-size:38px;font-weight:600;color:var(--ink);letter-spacing:-.3px}
.nav{position:absolute;top:36px;right:140px;display:flex;font-size:12.5px;font-weight:500;color:var(--blue)}
.nav a{color:inherit;text-decoration:none;margin-left:52px}
.nav a.active{color:var(--orange)}
/* hero */
.hero{top:88px;height:678px;background:radial-gradient(circle at 78% 45%,#3d8ff0 0%,#1556b8 25%,#0a3484 55%,var(--navy) 100%)}
.hero-art{position:absolute;left:520px;top:40px;width:680px;height:638px;background:radial-gradient(ellipse at 50% 50%,rgba(140,200,255,.55) 0%,rgba(60,130,230,.25) 40%,rgba(10,50,130,0) 70%)}
.hero-frame{position:absolute;left:92px;top:157px;width:451px;height:280px;border:1.5px solid rgba(255,255,255,.85)}
.hero-title{position:absolute;left:135px;top:196px;color:var(--white);font-weight:700;font-size:66px;line-height:68px;letter-spacing:1px}
.hero-sub{position:absolute;left:135px;top:348px;color:var(--white);font-weight:500;font-size:25px}
.btn-solid{position:absolute;background:var(--orange);color:var(--white);font-weight:600;text-align:center;border-radius:30px;letter-spacing:1px}
.hero .btn-solid{left:136px;top:412px;width:195px;height:43px;line-height:43px;font-size:14px}
/* about */
.about{top:766px;height:584px}
.about-shadow{position:absolute;left:140px;top:170px;width:415px;height:310px;background:var(--blue);border-radius:0 0 0 40px}
.about-photo{position:absolute;left:122px;top:94px;width:408px;height:362px;border-radius:0 56px 0 56px;background:radial-gradient(circle at 55% 55%,#ff8a0d 0%,#2b6fd0 18%,#0c2f74 55%,#061638 100%);box-shadow:0 12px 30px rgba(0,0,0,.25)}
.eyebrow{position:absolute;left:644px;top:138px;font-size:13px;font-weight:600;color:var(--blue);letter-spacing:1.5px}
.about-title{position:absolute;left:644px;top:158px;font-size:33px;font-weight:700;color:var(--ink)}
.about-rule{position:absolute;left:644px;top:206px;width:76px;height:3px;background:var(--orange)}
.about-copy{position:absolute;left:644px;top:238px;width:440px;font-size:14.2px;line-height:29px;color:var(--grey)}
.btn-outline-orange{position:absolute;left:648px;top:418px;width:168px;height:41px;border:2px solid var(--orange);color:var(--orange);font-size:14px;font-weight:600;text-align:center;line-height:37px;letter-spacing:1.5px}
/* services */
.services{top:1350px;height:648px;background:linear-gradient(180deg,var(--blue) 0%,#1f6fd8 60%,#4a8fe6 100%);color:var(--white)}
.services-wave{position:absolute;left:0;top:430px;width:1200px;height:218px;background:radial-gradient(ellipse at 50% 100%,rgba(180,215,255,.45) 0%,rgba(120,180,245,0) 70%)}
.services .heading{top:60px;color:var(--white)}
.services .rule{top:112px;background:var(--white)}
.service-hot{position:absolute;left:425px;top:165px;width:348px;height:363px;background:var(--orange);border-radius:44px 0 56px 0}
.service{position:absolute;width:300px;text-align:center}
.service-icon{margin:0 auto;width:124px;height:124px;border-radius:50%;background:var(--white);border:4px solid var(--white);box-shadow:inset 0 0 0 3px var(--blue);display:flex;align-items:center;justify-content:center}
.service-hot-wrap .service-icon{box-shadow:inset 0 0 0 3px var(--orange)}
.service h3{margin-top:18px;font-size:18px;font-weight:700;line-height:24px}
.service p{margin-top:10px;font-size:12.6px;line-height:20px;padding:0 12px}
.btn-outline-white{display:inline-block;margin-top:20px;width:142px;height:34px;border:2px solid var(--white);font-size:12px;font-weight:600;line-height:30px;letter-spacing:1px}
/* testimonials */
.testimonials{top:1998px;height:554px}
.testimonials .heading{top:78px}
.testimonials .rule{top:127px}
.quote-card{position:absolute;top:217px;width:306px;height:230px;border:1.5px solid var(--line);border-radius:3px;text-align:center}
.avatar{position:absolute;top:-38px;left:117px;width:72px;height:72px;border-radius:50%;border:3px solid var(--white);box-shadow:0 2px 6px rgba(0,0,0,.2)}
.quote-card p{margin:57px 28px 0;font-size:13.3px;line-height:20.5px;color:var(--grey)}
.quote-card h4{margin-top:18px;font-size:12.8px;font-weight:600;color:var(--ink)}
.dots{position:absolute;top:485px;left:572px;display:flex;gap:12px}
.dots span{width:11px;height:11px;border-radius:50%;background:#8fb2e8}
.dots span.on{background:var(--orange)}
/* blogs */
.blogs{top:2552px;height:621px;background:var(--pale)}
.blogs .heading{top:56px}
.blogs .rule{top:106px}
.blog-img{position:absolute;top:156px;width:308px;height:207px}
.blog-card{position:absolute;top:338px;width:272px;height:178px;background:var(--white);box-shadow:0 4px 14px rgba(30,60,120,.1);text-align:center}
.blog-date{position:absolute;top:-2px;left:92px;width:90px;height:20px;background:var(--blue);color:var(--white);font-size:10.5px;font-weight:600;line-height:20px}
.blog-card h4{margin:30px 18px 0;font-size:11.8px;font-weight:700;line-height:14px;color:var(--ink)}
.blog-card p{margin:12px 30px 0;font-size:9.5px;line-height:13px;color:var(--grey)}
.btn-pill{display:inline-block;margin-top:14px;width:112px;height:32px;border:2px solid var(--orange);border-radius:20px;color:var(--orange);font-size:9px;font-weight:600;line-height:28px}
/* faq */
.faq{top:3173px;height:701px}
.faq .heading{top:80px;font-size:28px}
.faq .rule{top:126px}
.faq-open{position:absolute;left:206px;top:170px;width:772px;height:149px;background:var(--orange);color:var(--white);padding:26px 34px}
.faq-open h4{font-size:12.5px;font-weight:600}
.faq-open p{margin-top:14px;font-size:11.5px;line-height:21px}
.faq-item{position:absolute;left:208px;width:770px;height:50px;border:2px solid #c8ced8;padding:0 34px;line-height:46px;font-size:11.8px;font-weight:600;color:#5a6272}
.chev{position:absolute;right:18px;top:12px}
.faq-open .chev{top:16px}
/* contact */
.contact{top:3874px;height:561px;background:linear-gradient(180deg,var(--blue) 0%,#1f6fd8 70%,#3a86e2 100%)}
.contact-wave{position:absolute;left:0;top:300px;width:1200px;height:261px;background:radial-gradient(ellipse at 50% 100%,rgba(180,215,255,.4) 0%,rgba(120,180,245,0) 70%)}
.contact .heading{top:60px;color:var(--white);font-size:28px}
.contact .rule{top:106px;background:var(--white)}
.field{position:absolute;background:var(--white);border-radius:30px;font-size:14.5px;color:#333;padding-left:16px;line-height:46px;height:46px;width:409px}
.field i{color:var(--orange);font-style:normal}
.message{position:absolute;left:188px;top:291px;width:825px;height:126px;background:var(--white);border-radius:14px;padding:18px 14px;font-size:14.5px;color:#333}
.contact .btn-solid{left:492px;top:444px;width:217px;height:45px;line-height:45px;font-size:15px}
/* footer */
.site-footer{top:4435px;height:384px;background:var(--black);color:var(--white)}
.foot-col{position:absolute;top:90px}
.foot-col h5{font-size:15px;font-weight:600;letter-spacing:.5px}
.foot-col ul{list-style:none;margin-top:18px}
.foot-col li{font-size:11.5px;line-height:32.5px;color:#d9d9d9}
.contact-row{position:absolute;left:0;display:flex;gap:14px}
.contact-row b{display:block;font-size:10.5px;font-weight:700}
.contact-row span{font-size:11px;color:#d9d9d9}
.foot-brand{position:absolute;left:896px;top:80px;font-size:38px;font-weight:600;color:var(--white)}
.socials{position:absolute;left:884px;top:170px;display:flex;gap:9px}
.socials span{width:30px;height:30px;border-radius:50%;background:var(--white)}
.socials span:first-child{background:var(--orange)}
.copy{position:absolute;right:132px;top:248px;text-align:right;font-size:11.5px;line-height:24px;color:#a9a9a9}
</style>
</head>
<body>

<header class="section site-header">
  <div class="brand">linkora</div>
  <nav class="nav">
    <a class="active">HOME</a><a>ABOUT US</a><a>SERVICES</a><a>TESTIMONIALS</a><a>FAQ</a><a>CONTACT</a>
  </nav>
</header>

<section class="section hero">
  <div class="hero-art" role="img" aria-label="Glowing digital chain link over a field of binary code"></div>
  <div class="hero-frame"></div>
  <h1 class="hero-title">LINKORA<br>SEO LINKS</h1>
  <p class="hero-sub">The Real done for you link</p>
  <div class="btn-solid">LEARN MORE</div>
</section>

<section class="section about">
  <div class="about-shadow"></div>
  <div class="about-photo" role="img" aria-label="Hand touching a glowing SEO button on a digital interface"></div>
  <div class="eyebrow">WHY WE ARE</div>
  <h2 class="about-title">ABOUT LINKORA</h2>
  <div class="about-rule"></div>
  <p class="about-copy">Lorem ipsum dolor sit amet, consectetur adipiscing elit, sed do eiusmod tempor incididunt ut labore et dolore magna aliqua. Ut enim ad minim veniam, quis nostrud exercitation ullamco laboris nisi Lorem ipsum dolor sit amet, consectetur adipiscing elit, sed do eiusmod</p>
  <div class="btn-outline-orange">LEARN MORE</div>
</section>

<section class="section services">
  <div class="services-wave" role="img" aria-label="Soft wave of light particles"></div>
  <h2 class="heading">OUR SERVICES</h2>
  <div class="rule"></div>
  <div class="service-hot"></div>

  <div class="service" style="left:105px;top:205px">
    <div class="service-icon">
      <svg width="54" height="54" viewBox="0 0 54 54" fill="none" stroke="#1f6fd8" stroke-width="2.4" stroke-linejoin="round"><rect x="4" y="7" width="44" height="34" rx="3"/><line x1="4" y1="15" x2="48" y2="15"/><circle cx="9" cy="11" r="1"/><circle cx="14" cy="11" r="1"/><rect x="11" y="21" width="14" height="10"/><path d="M30 27 l14 6 -6 2 -2 6 z"/></svg>
    </div>
    <h3>Premium Links</h3>
    <p>Lorem ipsum dolor sit amet, consectetur adipiscing elit, sed do eiusmod tempor incididunt u</p>
    <div class="btn-outline-white">LEARN MORE</div>
  </div>

  <div class="service service-hot-wrap" style="left:449px;top:205px">
    <div class="service-icon">
      <svg width="56" height="56" viewBox="0 0 56 56" fill="none" stroke="#ff8a0d" stroke-width="2.4" stroke-linejoin="round"><rect x="5" y="9" width="40" height="36" rx="2"/><line x1="5" y1="18" x2="45" y2="18"/><line x1="14" y1="5" x2="14" y2="13"/><line x1="36" y1="5" x2="36" y2="13"/><path d="M12 25h5M22 25h5M32 25h5M12 32h5M22 32h5M12 39h5"/><circle cx="41" cy="40" r="9" fill="#fff"/><path d="M37 40l3 3 5-6"/></svg>
    </div>
    <h3>Monthly Links<br>Subscription</h3>
    <p style="margin-top:8px">Lorem ipsum dolor sit amet, consectetur adipiscing elit, sed do eius</p>
    <div class="btn-outline-white" style="margin-top:18px">LEARN MORE</div>
  </div>

  <div class="service" style="left:794px;top:205px">
    <div class="service-icon">
      <svg width="58" height="58" viewBox="0 0 58 58" fill="none" stroke="#1f6fd8" stroke-width="3" stroke-linecap="round"><rect x="8" y="24" width="24" height="13" rx="6.5" transform="rotate(-45 20 30)"/><rect x="26" y="21" width="24" height="13" rx="6.5" transform="rotate(-45 38 28)"/><line x1="24" y1="34" x2="34" y2="24"/></svg>
    </div>
    <h3>Link Insertions</h3>
    <p style="margin-top:4px">Lorem ipsum dolor sit amet, consectetur adipiscing elit, sed do eiusmod tempor incididunt ut l</p>
    <div class="btn-outline-white" style="margin-top:14px">LEARN MORE</div>
  </div>
</section>

<section class="section testimonials">
  <h2 class="heading">TESTIMONIALS</h2>
  <div class="rule"></div>
  <div class="quote-card" style="left:122px">
    <div class="avatar" role="img" aria-label="Client portrait" style="background:#8a97a8"></div>
    <p>Lorem ipsum dolor sit amet, consectetur adipiscing elit, sed do eiusmod tempor incididunt ut labore et dolore magna aliqua. Ut enim ad minim veniam, quis nostrud</p>
    <h4>OWEN HARTLETT</h4>
  </div>
  <div class="quote-card" style="left:446px">
    <div class="avatar" role="img" aria-label="Client portrait" style="background:#6b4a3a"></div>
    <p>Lorem ipsum dolor sit amet, consectetur adipiscing elit, sed do eiusmod tempor incididunt ut labore et dolore magna aliqua. Ut enim ad minim veniam, quis nostrud</p>
    <h4>REID GALLOWAY</h4>
  </div>
  <div class="quote-card" style="left:770px">
    <div class="avatar" role="img" aria-label="Client portrait" style="background:#3e2a20"></div>
    <p>Lorem ipsum dolor sit amet, consectetur adipiscing elit, sed do eiusmod tempor incididunt ut labore et dolore magna aliqua. Ut enim ad minim veniam, quis nostrud</p>
    <h4>TOMAS LINDQVIST</h4>
  </div>
  <div class="dots"><span></span><span></span><span class="on"></span></div>
</section>

<section class="section blogs">
  <h2 class="heading">LATEST BLOGS</h2>
  <div class="rule"></div>

  <div class="blog-img" role="img" aria-label="Blue circuit board with SEO icons" style="left:124px;background:linear-gradient(135deg,#0c2a5e,#1d5fb8 60%,#0a1f48)"></div>
  <div class="blog-card" style="left:144px">
    <div class="blog-date">12 SEP 2020</div>
    <h4>Lorem ipsum dolor sit amet, consectetur adipiscing elit, sed do</h4>
    <p>Lorem ipsum dolor sit amet, consectetur adipiscing elit, sed do eiusmod tempor</p>
    <div class="btn-pill">LEARN MORE</div>
  </div>

  <div class="blog-img" role="img" aria-label="Hand holding a pen over an SEO search bar" style="left:450px;background:linear-gradient(135deg,#7d5a4a,#c8a898 45%,#e6dcd6)"></div>
  <div class="blog-card" style="left:470px">
    <div class="blog-date">12 SEP 2020</div>
    <h4>Lorem ipsum dolor sit amet, consectetur adipiscing elit, sed do</h4>
    <p>Lorem ipsum dolor sit amet, consectetur adipiscing elit, sed do eiusmod tempor</p>
    <div class="btn-pill">LEARN MORE</div>
  </div>

  <div class="blog-img" role="img" aria-label="Hands on a laptop with floating SEO icons" style="left:776px;background:linear-gradient(135deg,#2e5fa8,#8fb4e0 50%,#d28a6a)"></div>
  <div class="blog-card" style="left:796px">
    <div class="blog-date">12 SEP 2020</div>
    <h4>Lorem ipsum dolor sit amet, consectetur adipiscing elit, sed do</h4>
    <p>Lorem ipsum dolor sit amet, consectetur adipiscing elit, sed do eiusmod tempor</p>
    <div class="btn-pill">LEARN MORE</div>
  </div>
</section>

<section class="section faq">
  <h2 class="heading">FREQUENTLY ASKED QUESTIONS</h2>
  <div class="rule"></div>
  <div class="faq-open">
    <h4>Lorem ipsum dolor sit amet, consectetur adipiscing elit ?</h4>
    <p>Sed ut perspiciatis unde omnis iste natus error sit voluptatem accusantium doloremque laudantium, totam rem aperiam, eaque ipsa quae ab illo inventore veritatis et quasi architecto beatae vitae dicta sunt explicabo. Nemo enim ipsam voluptatem quia voluptas sit aspernatur aut odit aut fugit, sed quia consequuntur magni dolores eos</p>
    <svg class="chev" width="24" height="24" viewBox="0 0 24 24" fill="none" stroke="#fff" stroke-width="1.5"><circle cx="12" cy="12" r="10.5"/><path d="M7.5 14l4.5-4.5 4.5 4.5"/></svg>
  </div>
  <div class="faq-item" style="top:335px">Sed ut perspiciatis unde omnis iste natus ?
    <svg class="chev" width="24" height="24" viewBox="0 0 24 24" fill="none" stroke="#1f6fd8" stroke-width="1.5"><circle cx="12" cy="12" r="10.5"/><path d="M7.5 10l4.5 4.5 4.5-4.5"/></svg></div>
  <div class="faq-item" style="top:395px">Error sit voluptatem accusantium doloremque laudantium ?
    <svg class="chev" width="24" height="24" viewBox="0 0 24 24" fill="none" stroke="#1f6fd8" stroke-width="1.5"><circle cx="12" cy="12" r="10.5"/><path d="M7.5 10l4.5 4.5 4.5-4.5"/></svg></div>
  <div class="faq-item" style="top:455px">Ttotam rem aperiam, eaque ipsa quae ab illo inventore ?
    <svg class="chev" width="24" height="24" viewBox="0 0 24 24" fill="none" stroke="#1f6fd8" stroke-width="1.5"><circle cx="12" cy="12" r="10.5"/><path d="M7.5 10l4.5 4.5 4.5-4.5"/></svg></div>
  <div class="faq-item" style="top:515px">Weritatis et quasi architecto beatae vitae dicta ?
    <svg class="chev" width="24" height="24" viewBox="0 0 24 24" fill="none" stroke="#1f6fd8" stroke-width="1.5"><circle cx="12" cy="12" r="10.5"/><path d="M7.5 10l4.5 4.5 4.5-4.5"/></svg></div>
</section>

<section class="section contact">
  <div class="contact-wave" role="img" aria-label="Soft wave of light particles"></div>
  <h2 class="heading">FILL OUR CONTACT FORM</h2>
  <div class="rule"></div>
  <div class="field" style="left:182px;top:151px">First Name<i>*</i></div>
  <div class="field" style="left:600px;top:151px;padding-left:38px">Last Name<i>*</i></div>
  <div class="field" style="left:182px;top:220px">Contact Number<i>*</i></div>
  <div class="field" style="left:600px;top:220px;padding-left:38px">E-mail<i>*</i></div>
  <div class="message">Leave a Message</div>
  <div class="btn-solid">SEND MESSAGE</div>
</section>

<footer class="section site-footer">
  <div class="foot-col" style="left:154px">
    <h5>INFORMATION</h5>
    <ul><li>Home</li><li>About Us</li><li>Services</li><li>News &amp; Blogs</li><li>Contact</li></ul>
  </div>
  <div class="foot-col" style="left:369px">
    <h5>LINKS</h5>
    <ul><li>Careers</li><li>Support</li><li>Sitemap</li><li>Privacy Policy</li><li>Contact Us</li></ul>
  </div>
  <div class="foot-col" style="left:558px;width:320px">
    <h5>CONTACT US</h5>
    <div class="contact-row" style="top:40px">
      <svg width="30" height="30" viewBox="0 0 30 30" fill="none" stroke="#fff" stroke-width="1.5"><path d="M15 4a7 7 0 0 1 7 7c0 5-7 12-7 12s-7-7-7-12a7 7 0 0 1 7-7z"/><circle cx="15" cy="11" r="2.5"/><ellipse cx="15" cy="25" rx="10" ry="3"/></svg>
      <div><b>ADDRESS</b><span>418 Alder Crest Lane Marwick</span></div>
    </div>
    <div class="contact-row" style="top:98px">
      <svg width="30" height="30" viewBox="0 0 30 30" fill="none" stroke="#fff" stroke-width="1.5"><path d="M8 4l4 5-2.5 3a14 14 0 0 0 8.5 8.5l3-2.5 5 4-2 4c-10 0-20-10-20-20z"/></svg>
      <div><b>PHONE</b><span style="font-size:13px">(555)-410-7782</span></div>
    </div>
    <div class="contact-row" style="top:156px">
      <svg width="30" height="30" viewBox="0 0 30 30" fill="none" stroke="#fff" stroke-width="1.5"><rect x="3" y="7" width="24" height="17"/><path d="M3 7l12 10 12-10"/></svg>
      <div><b>EMAIL US</b><span style="font-size:13px">hello@linkora.com</span></div>
    </div>
  </div>
  <div class="foot-brand">linkora</div>
  <div class="socials"><span></span><span></span><span></span><span></span><span></span></div>
  <div class="copy">Copyright © 2021 Linkora.<br>All Right Reserved</div>
</footer>

</body>
</html>
```